American cannabis tech company business card design

Pavrel.com is seeking a modern, professional, and brand-aligned business card that represents our company and its core values: Mission, Story, Values, and Impact. As an innovative cannabis company, we want a business card that is not only visually appealing but also serves as a representation of who we are and what we stand for.

Project Scope: Design a double-sided business card that integrates our brand identity and core values. Incorporate our key brand elements, ensuring a sleek and contemporary aesthetic. Visually reflect our core values (Mission, Story, Values, Impact) in a way that is engaging yet professional.

Target Market(s)

Vendors, third parties,

Contact Information for Business Card

Contact details (name, title, email, phone, website, etc.)

Font styles to use
Other font styles liked:
• Caslon, Centra

Colors

Designer to choose colors to be used in the design.

Requirements
Must have
• Pavrel.com logo and branding A creative yet clean way to integrate our core values (Mission, Story, Values, Impact) Modern typography and a well-structured layout
Nice to have
• forest green, grey, white, black
Should not have
• references to marijuana, leafs, plants, or related product

```html
<!DOCTYPE html>
<html lang="en">
<head>
<meta charset="utf-8">
<title>Pavrel.com Business Card</title>
<link href="https://fonts.googleapis.com/css2?family=Montserrat:wght@400;500&family=Playfair+Display:wght@700;900&display=swap" rel="stylesheet">
<style>
  :root {
    --forest: #1b3520;
    --forest-deep: #13291a;
    --paper: #ffffff;
    --backdrop: #1c1c1c;
  }
  * { margin: 0; padding: 0; box-sizing: border-box; }
  html, body {
    width: 1200px; height: 1059px; overflow: hidden;
    background: var(--backdrop);
  }
  .card {
    position: absolute; left: 253px; width: 692px; height: 395px;
    border-radius: 18px; overflow: hidden;
  }
  .card-front { top: 89px; background: var(--paper); }
  .card-back { top: 546px; background: var(--forest); }
  .wave { position: absolute; inset: 0; width: 100%; height: 100%; }
  .wordmark {
    position: absolute; font-family: "Playfair Display", serif; font-weight: 900;
    letter-spacing: 1px; line-height: 1;
  }
  .card-front .wordmark { right: 32px; top: 40px; font-size: 74px; color: var(--forest); }
  .card-back .wordmark {
    left: 0; right: 0; top: 150px; text-align: center;
    font-size: 112px; color: var(--forest-deep);
  }
  .holder { position: absolute; left: 35px; top: 186px; color: var(--paper); }
  .holder-name { font-family: "Playfair Display", serif; font-weight: 700; font-size: 23px; }
  .holder-title { font-family: "Playfair Display", serif; font-weight: 700; font-size: 12px; letter-spacing: .5px; margin-top: 1px; }
  .address {
    position: absolute; left: 32px; top: 246px; color: var(--paper);
    font-family: "Montserrat", sans-serif; font-size: 15px; line-height: 18px;
  }
  .contact-list {
    position: absolute; left: 34px; top: 300px; list-style: none; color: var(--paper);
    font-family: "Montserrat", sans-serif; font-size: 15px;
  }
  .contact-list li { display: flex; align-items: center; height: 25.5px; gap: 9px; }
  .contact-list svg { width: 14px; height: 14px; fill: var(--paper); }
</style>
</head>
<body>

<section class="card card-front">
  <svg class="wave" viewBox="0 0 1175 671" preserveAspectRatio="none" aria-hidden="true">
    <path fill="var(--forest)" d="M0,228 C90,195 180,180 260,195 C400,220 520,320 700,400 C820,450 960,450 1050,390 C1110,350 1150,290 1175,245 L1175,671 L0,671 Z"/>
    <path fill="none" stroke="#ffffff" stroke-width="6" d="M0,290 C100,250 200,235 300,255 C420,280 560,380 720,460 C860,525 1000,530 1175,375"/>
    <path fill="none" stroke="#ffffff" stroke-width="4" d="M490,300 C600,370 700,440 800,478 C950,522 1080,480 1175,388"/>
  </svg>

  <div class="wordmark">PAVREL</div>

  <div class="holder">
    <div class="holder-name">Daniel Ortiz</div>
    <div class="holder-title">Owner</div>
  </div>

  <div class="address">
    418 Birchwood Ave, #114<br>
    Lakeview, OH 43210
  </div>

  <ul class="contact-list">
    <li>
      <svg viewBox="0 0 24 24"><path d="M6.6 10.8a15.1 15.1 0 0 0 6.6 6.6l2.2-2.2a1 1 0 0 1 1-.25 11.4 11.4 0 0 0 3.6.57 1 1 0 0 1 1 1V20a1 1 0 0 1-1 1A17 17 0 0 1 3 4a1 1 0 0 1 1-1h3.5a1 1 0 0 1 1 1c0 1.25.2 2.45.57 3.57a1 1 0 0 1-.25 1z"/></svg>
      555-318-0427
    </li>
    <li>
      <svg viewBox="0 0 24 24"><path d="M2 5h20v14H2z M2 5l10 7 10-7" stroke="#1b3520" stroke-width="1.5"/></svg>
      info@pavrel.com
    </li>
    <li>
      <svg viewBox="0 0 24 24"><path d="M12 2a10 10 0 1 0 0 20 10 10 0 0 0 0-20zm-1 17.9A8 8 0 0 1 4.1 9.5L9 14.4v1a2 2 0 0 0 2 2zm6.9-2.5A2 2 0 0 0 16 16h-1v-3a1 1 0 0 0-1-1H8v-2h2a1 1 0 0 0 1-1V7h2a2 2 0 0 0 2-2v-.4a8 8 0 0 1 2.9 12.8z"/></svg>
      www.pavrel.com
    </li>
  </ul>
</section>

<section class="card card-back">
  <div class="wordmark">PAVREL</div>
</section>

</body>
</html>
```